National Sales - Pick Up Truck Dealer

We need a logo design for a new vehicle dealership based in Sydney, Australia. The business name is Coastal Iron Haulers Motor Co. We will be selling American 'trucks/pick up trucks' like KRV, Torvan, Blaxer, Morrow T420, Kenzo Raptors, Morrow T640 and the likes.

These vehicles are a luxury option and we would like the logo to be strong, luxurious and masculine.Colours will be black and red or black and blue with the option of grey and white.

Target Market(s)

Men

Industry/Entity Type

Car Dealer

Contact Information for Business Card

Dennis Harlowe
Managing Director
0412 639 274
den@qelvtrk.com.au

Level 5, Brindle Parkway
17 Pemberly Lane
Baulkham Hills
NSW
Australia
Licence No: MD493152

Back of the card

qelvtrk.com.au

Font styles to use
Sans Serif

Colors

Designer to choose colors to be used in the design.

Requirements
Must have
• The company logo that is in the attachments, you can choose from the three which one you would like to work with. Must have vehicle images ....Please look at the attachments as they show examples of what we like and also provides potential images. If you choose to put an image on the front even if it is just the front of the vehicle can you please use the Black KRV Sorrento. Must have all details from the business card details section front and back
Nice to have
• N/A
Should not have
• No cars or standard trucks, please refer to the attached images to understand the product . Should not have any new logos or branding. No other colours besides what is in the logo you choose.

```html
<!DOCTYPE html>
<html lang="en">
<head>
<meta charset="utf-8">
<title>Coastal Iron Haulers Motor Co — Business Card</title>
<link rel="stylesheet" href="https://fonts.googleapis.com/css2?family=Maven+Pro:wght@500;600;700&display=swap">
<style>
  :root {
    --backdrop: #7a5539;
    --card-white: #f4f5f6;
    --card-white-edge: #e6e8ea;
    --ink-dark: #1e1f21;
    --ink-grey: #4f5154;
    --brand-blue: #1f78b8;
    --brand-blue-light: #35a4de;
    --strip-dark: #222325;
    --card-black: #0b0c0d;
    --card-black-mid: #1b1d1f;
    --truck-navy: #1d2a66;
    --truck-black: #111214;
    --white: #ffffff;
  }
  * { box-sizing: border-box; margin: 0; padding: 0; }
  html, body { width: 1200px; height: 960px; overflow: hidden; }
  body {
    background: var(--backdrop);
    font-family: "Maven Pro", Arial, sans-serif;
    position: relative;
  }
  .card {
    position: absolute;
    width: 600px;
    height: 342px;
    overflow: hidden;
    box-shadow: 0 3px 8px rgba(0,0,0,0.35);
  }
  /* Front */
  .card--front {
    left: 322px; top: 110px;
    background: linear-gradient(180deg, var(--card-white) 0%, var(--card-white-edge) 100%);
  }
  .edge-strip { position: absolute; left: 0; top: 0; width: 16px; height: 342px; }
  .truck-photo {
    position: absolute; left: 250px; top: 20px; width: 350px; height: 322px;
    clip-path: polygon(45% 0, 100% 0, 100% 100%, 0 100%, 0 32%, 20% 14%);
    background:
      radial-gradient(ellipse at 50% 35%, #2b3c86 0%, var(--truck-navy) 40%, transparent 75%),
      linear-gradient(180deg, #1a2457 0%, var(--truck-black) 70%, #2a2b2d 100%);
  }
  .front-wordmark {
    position: absolute; left: 38px; top: 44px; width: 240px;
    z-index: 1;
    text-align: center;
    font-weight: 700; font-size: 17px; line-height: 22px;
    letter-spacing: 0.4px; color: var(--ink-dark);
    text-transform: uppercase;
  }
  .contact { position: absolute; left: 40px; top: 154px; z-index: 1; }
  .contact__name {
    font-weight: 600; font-size: 19px; color: var(--brand-blue);
    text-transform: uppercase; letter-spacing: 0.2px;
  }
  .contact__title {
    margin-top: 2px;
    font-weight: 700; font-size: 14.5px; color: var(--ink-dark);
    text-transform: uppercase;
  }
  .contact__address {
    margin-top: 14px;
    font-style: normal; font-weight: 500; font-size: 14.5px;
    line-height: 19.7px; color: var(--ink-grey);
  }
  .contact__phone {
    margin-top: 6px;
    display: flex; align-items: center; gap: 8px;
    font-weight: 600; font-size: 15px; color: var(--ink-grey);
  }
  .contact__phone svg { width: 14px; height: 14px; }
  /* Back */
  .card--back {
    left: 320px; top: 493px;
    background: radial-gradient(ellipse at 50% 35%, var(--card-black-mid) 0%, var(--card-black) 70%);
  }
  .back-wordmark {
    position: absolute; left: 0; right: 0; top: 118px;
    text-align: center;
    font-weight: 700; font-size: 36px; line-height: 44px;
    letter-spacing: 1px; color: var(--white);
    text-transform: uppercase;
  }
  .back-url {
    position: absolute; left: 0; right: 0; top: 282px;
    text-align: center;
    font-weight: 600; font-size: 21px; letter-spacing: 0.5px;
    color: var(--brand-blue-light); text-transform: uppercase;
  }
</style>
</head>
<body>
  <section class="card card--front" aria-label="Business card front">
    <svg class="edge-strip" viewBox="0 0 16 342" preserveAspectRatio="none" aria-hidden="true">
      <defs>
        <linearGradient id="stripBlue" x1="0" y1="0" x2="0" y2="1">
          <stop offset="0" stop-color="#35a4de"/>
          <stop offset="1" stop-color="#1a5f98"/>
        </linearGradient>
      </defs>
      <polygon points="0,0 16,0 16,136 0,122" fill="#222325"/>
      <polygon points="0,122 16,136 16,342 0,342" fill="url(#stripBlue)"/>
    </svg>

    <div class="truck-photo" role="img" aria-label="Photo of the front of a dark pickup truck"></div>

    <div class="front-wordmark">Coastal Iron Haulers<br>Motor Co</div>

    <div class="contact">
      <p class="contact__name">Dennis Harlowe</p>
      <p class="contact__title">Managing Director</p>
      <address class="contact__address">
        Level 5, Brindle Parkway<br>
        17 Pemberly Lane<br>
        Baulkham Hills<br>
        NSW, Australia
      </address>
      <p class="contact__phone">
        <svg viewBox="0 0 24 24" aria-hidden="true"><path fill="#1f78b8" d="M6.6 10.8a15 15 0 0 0 6.6 6.6l2.2-2.2a1 1 0 0 1 1-.25 11.4 11.4 0 0 0 3.6.57 1 1 0 0 1 1 1V20a1 1 0 0 1-1 1A17 17 0 0 1 3 4a1 1 0 0 1 1-1h3.5a1 1 0 0 1 1 1c0 1.25.2 2.45.57 3.57a1 1 0 0 1-.25 1z"/></svg>
        0412 639 274
      </p>
    </div>
  </section>

  <section class="card card--back" aria-label="Business card back">
    <div class="back-wordmark">Coastal Iron Haulers<br>Motor Co</div>
    <p class="back-url">qelvtrk.com.au</p>
  </section>
</body>
</html>
```